A website for a Maltese Law Firm

Our law firm needs a website to further its business. The site should have a simple yet effective design. We would need the following sections: About us, Practice Areas, About Malta, Contact. These should be further split as follows:

About us: Our firm, Our values, What others say, Offices

Practice Areas: Crimimal, Citizenship & Residence, Sovereign Patron Pathway, Criminal Defence, Civil Litigation, Arbitration and ADR, Commercial and Corporate, Media Law.

About Malta: just one section.

Contact: Just one section

We would also need a news feed at the front of the site to include latest news regarding our cases.

At the bottom we need a section for our Terms and a Privacy Statement.

Our logo is being attached.

Target Market(s)

All clients looking for legal assistance in Malta

Industry/Entity Type

Legal

Coding

Coded - Design and coding required

Number of Pages Required

1 page

Requirements
Must have
• It must be simple yet striking.

```html
<!DOCTYPE html>
<html lang="en">
<head>
<meta charset="utf-8">
<title>Galea &amp; Mifsud Advocates</title>
<link rel="stylesheet" href="https://fonts.googleapis.com/css2?family=Cinzel:wght@400;700&family=Lato:ital,wght@0,400;0,700;1,400&family=Oswald:wght@400&display=swap">
<style>
:root{
  --ink:#2b2d33;
  --dark:#2e3038;
  --nav:#2f3139;
  --nav-active:#a5a6aa;
  --grey-band:#ebebeb;
  --cta:#a9aaae;
  --foot:#2e3038;
  --foot-bar:#a3a4a8;
  --white:#ffffff;
  --line:#4a4c55;
  --text:#333333;
  --muted:#555;
}
*{margin:0;padding:0;box-sizing:border-box}
html,body{width:1200px;height:2723px;overflow:hidden}
body{background:var(--white);font-family:"Lato",sans-serif;color:var(--text);position:relative}
.abs{position:absolute}
.serif{font-family:"Cinzel",serif}

/* header */
.site-header{position:absolute;top:0;left:0;width:1200px;height:107px;background:var(--white)}
.brand{position:absolute;left:73px;top:30px;font-family:"Cinzel",serif;font-size:34px;color:var(--ink);letter-spacing:1px;line-height:1}
.brand small{display:block;font-size:15px;letter-spacing:6px;text-align:center;margin-top:6px}
.head-contact{position:absolute;left:898px;top:22px;font-size:17px;font-weight:700;color:var(--ink)}
.head-contact div{display:flex;align-items:center;gap:10px;height:34px}
.head-contact svg{width:24px;height:24px}

/* nav */
.main-nav{position:absolute;top:107px;left:0;width:1200px;height:44px;background:var(--nav)}
.main-nav ul{list-style:none;position:absolute;left:67px;top:0;display:flex;height:44px}
.main-nav li{font-family:"Cinzel",serif;font-size:15px;color:var(--white);display:flex;align-items:center;justify-content:center;border-right:1px solid #5b5d66;height:44px}
.main-nav li.active{background:var(--nav-active);color:var(--ink)}

/* hero */
.hero{position:absolute;top:151px;left:0;width:1200px;height:426px;background:linear-gradient(110deg,#3a1c0c 0%,#7a4a22 30%,#b98a55 55%,#d8b889 75%,#c49a68 100%)}
.hero-title{position:absolute;right:71px;top:128px;text-align:right;font-family:"Oswald",sans-serif;font-size:40px;line-height:52px;color:var(--white)}
.hero-btn{position:absolute;left:793px;top:270px;width:336px;height:51px;background:#3b3c40;border:2px solid #d8d8d8;color:var(--white);font-family:"Cinzel",serif;font-size:22px;display:flex;align-items:center;justify-content:center}
.hero-dot{position:absolute;left:1080px;top:345px;width:50px;height:3px;background:#ddd}

/* welcome */
.welcome{position:absolute;top:577px;left:0;width:1200px;height:452px;background:var(--grey-band)}
.welcome h1{position:absolute;left:69px;top:60px;font-family:"Cinzel",serif;font-weight:400;font-size:29px;color:var(--ink)}
.welcome .lead{position:absolute;left:69px;top:114px;width:680px;font-size:16px;line-height:24px;color:#222}
.welcome .body{position:absolute;left:69px;top:178px;width:680px;font-size:13.5px;line-height:22px;color:#333}
.pill-btn{position:absolute;height:29px;display:flex;align-items:center}
.pill-btn span{background:#a7a8ac;border:1px solid #777;height:27px;line-height:25px;padding:0 36px 0 10px;font-size:12px;font-weight:700;color:var(--ink);text-transform:uppercase}
.pill-btn i{width:31px;height:31px;border-radius:50%;background:var(--dark);margin-left:-22px;display:flex;align-items:center;justify-content:center}
.eval{position:absolute;left:797px;top:62px;width:330px;height:325px;border:2px solid var(--ink)}
.eval h2{font-family:"Cinzel",serif;font-weight:400;font-size:23px;color:var(--ink);margin:22px 0 0 17px}
.eval .field{position:absolute;left:17px;width:292px;background:var(--white);border:1px solid #ccc;font-size:13px;color:#444;padding:8px 10px}

/* practice */
.practice{position:absolute;top:1029px;left:0;width:1200px;height:423px;background:var(--white)}
.sec-title{position:absolute;left:0;width:1200px;text-align:center;font-family:"Cinzel",serif;font-size:29px;color:var(--ink)}
.area{position:absolute;top:124px;width:270px;text-align:center}
.area .icon{width:100px;height:100px;margin:0 auto;border:3px solid var(--ink);display:flex;align-items:center;justify-content:center;background:var(--white)}
.area .icon.on{background:var(--dark)}
.area h3{font-family:"Cinzel",serif;font-weight:400;font-size:20px;color:var(--ink);margin-top:20px}
.area p{font-size:14px;line-height:18px;width:200px;margin:6px auto 0;color:#222}
.area .more{font-size:15px;margin-top:10px;color:#222}
.chev{position:absolute;width:20px;height:60px}

/* case studies */
.cases{position:absolute;top:1452px;left:0;width:1200px;height:526px;background:var(--grey-band)}
.case{position:absolute;top:124px;width:312px}
.case .photo{height:163px;border:5px solid var(--white);outline:1px solid #c9c9c9;position:relative}
.case .date{position:absolute;left:7px;top:6px;width:50px;background:var(--dark);color:var(--white);font-size:19px;font-weight:700;text-align:center;line-height:24px}
.case .date span{display:block;background:var(--white);color:#222;font-size:14px;font-weight:400;line-height:22px}
.case h4{font-size:13.5px;font-weight:700;color:#111;margin-top:16px}
.case p{font-size:12.5px;line-height:19px;margin-top:8px;color:#333}
.case .read{font-size:12.5px;margin-top:8px;color:#222}

/* testimonials */
.testimonials{position:absolute;top:1978px;left:0;width:1200px;height:304px;background:var(--white)}
.portrait{position:absolute;left:134px;top:122px;width:116px;height:116px;background:linear-gradient(180deg,#e8e8e8,#bfc3c9 60%,#2f3440)}
.quote{position:absolute;left:312px;top:120px;width:760px;font-style:italic;font-size:13.5px;line-height:22px;color:#222}
.qmark{position:absolute;font-family:"Cinzel",serif;font-size:70px;color:#ddd;line-height:1}
.client{position:absolute;left:312px;top:221px;font-family:"Cinzel",serif;font-size:19px;color:#222}

/* cta */
.cta{position:absolute;top:2282px;left:0;width:1200px;height:128px;background:var(--cta)}
.cta p{position:absolute;left:116px;top:30px;font-family:"Cinzel",serif;font-size:28px;line-height:36px;color:var(--white)}
.cta .btn{position:absolute;left:844px;top:39px;width:223px;height:46px;background:var(--dark);border:2px solid #ddd;color:var(--white);font-weight:700;font-size:23px;display:flex;align-items:center;justify-content:center}

/* footer */
.site-footer{position:absolute;top:2410px;left:0;width:1200px;height:267px;background:var(--foot);color:var(--white)}
.site-footer h5{position:absolute;top:43px;font-family:"Cinzel",serif;font-weight:400;font-size:17px;padding-bottom:8px;border-bottom:1px solid var(--line)}
.quick{position:absolute;left:67px;top:90px;list-style:none;font-size:12px;font-weight:700}
.quick li{height:24px}
.quick li::before{content:"";display:inline-block;width:5px;height:5px;background:var(--white);border-radius:50%;margin-right:10px;vertical-align:middle}
.map{position:absolute;left:301px;top:86px;width:258px;height:125px;background:linear-gradient(135deg,#f1eee6,#dcd9cf 50%,#c7d6e6)}
.details{position:absolute;left:592px;top:86px;font-size:12.5px;font-weight:700;line-height:19px}
.details .row{display:flex;gap:14px;margin-bottom:8px}
.details svg{width:14px;height:14px;flex:none;margin-top:3px}
.foot-brand{position:absolute;left:886px;top:98px;width:242px;text-align:center;font-family:"Cinzel",serif;font-size:25px;color:var(--white);line-height:1}
.foot-brand small{display:block;font-size:11px;letter-spacing:5px;margin-top:4px}
.social{position:absolute;top:150px;left:924px;display:flex;gap:12px}
.social span{width:32px;height:32px;border-radius:50%;border:2px solid #fff}
.legal{position:absolute;top:2677px;left:0;width:1200px;height:46px;background:var(--foot-bar);font-size:12.5px;color:#222}
.legal .copy{position:absolute;left:69px;top:15px}
.legal .links{position:absolute;right:71px;top:15px}
</style>
</head>
<body>

<header class="site-header">
  <div class="brand">Galea &amp; Mifsud<small>Advocates</small></div>
  <div class="head-contact">
    <div><svg viewBox="0 0 24 24"><rect x="2" y="2" width="20" height="20" rx="4" fill="#2b2d33"/><rect x="8" y="5" width="8" height="14" rx="1" fill="#fff"/></svg>555-010-2040</div>
    <div><svg viewBox="0 0 24 24"><rect x="2" y="2" width="20" height="20" rx="4" fill="#2b2d33"/><rect x="6" y="8" width="12" height="8" fill="#fff"/><path d="M6 8l6 5 6-5" stroke="#2b2d33" fill="none"/></svg>info@galeamifsud.com</div>
  </div>
</header>

<nav class="main-nav">
  <ul>
    <li class="active" style="width:93px">Home</li>
    <li style="width:161px">About Malta</li>
    <li style="width:184px">Practice Areas</li>
    <li style="width:125px">Our Firm</li>
    <li style="width:145px">Our Values</li>
    <li style="width:202px">What Others Say</li>
    <li style="width:152px">Contact Us</li>
  </ul>
</nav>

<section class="hero" role="img" aria-label="Wooden judge's gavel resting on a contract document">
  <div class="hero-title">Realize Your Constitutional<br>Right For Qualified Legal Help</div>
  <div class="hero-btn">Get A Free Consultation</div>
  <div class="hero-dot"></div>
</section>

<section class="welcome">
  <h1>Welcome To Galea &amp; Mifsud Advocates</h1>
  <p class="lead">Lorem ipsum dolor sit amet, consectetuer adipiscing elit, sed diam nonummy nibh euismod tincidunt ut laoreet dolore magna aliquam erat volutpat.</p>
  <p class="body">Lorem ipsum dolor sit amet, consectetur adipiscing elit. Sed vitae magna tellus. Aenean ante nunc, semper nec cursus non, rutrum ac eros. Vestibulum mattis justo ac dui bibendum consequat a ac ipsum. Praesent a arcu venenatis, auctor velit eu, suscipit libero. Quisque convallis, leo ac pharetra sagittis, ipsum arcu auctor urna, sit amet cursus risus augue in eros. Duis lacinia nisi vitae leo commodo, non finibus magna maximus. Sed posuere, neque eget bibendum pulvinar, ligula erat suscipit dolor, ut maximus arcu mi et tortor. Quisque imperdiet turpis et ligula mollis ultricies. Mauris lacinia rhoncus odio, at rutrum diam mollis eu. Quisque ut ipsum faucibus, tristique dui vitae, posuere orci.</p>
  <div class="pill-btn" style="left:69px;top:360px"><span>Read More</span><i><svg width="10" height="12" viewBox="0 0 10 12"><path d="M2 1l5 5-5 5" stroke="#fff" stroke-width="2" fill="none"/></svg></i></div>

  <form class="eval">
    <h2>Free Case Evaluation</h2>
    <div class="field" style="top:82px;height:40px">Name</div>
    <div class="field" style="top:131px;height:40px">Email</div>
    <div class="field" style="top:180px;height:76px">Message</div>
    <div class="pill-btn" style="left:17px;top:272px"><span style="font-size:14px">Submit</span><i><svg width="10" height="12" viewBox="0 0 10 12"><path d="M2 1l5 5-5 5" stroke="#fff" stroke-width="2" fill="none"/></svg></i></div>
  </form>
</section>

<section class="practice">
  <h2 class="sec-title" style="top:56px">Our Practice Areas</h2>
  <svg class="chev" style="left:28px;top:212px" viewBox="0 0 20 60"><path d="M16 2L4 30l12 28" stroke="#444" stroke-width="1.5" fill="none"/></svg>
  <svg class="chev" style="left:1152px;top:212px" viewBox="0 0 20 60"><path d="M4 2l12 28L4 58" stroke="#444" stroke-width="1.5" fill="none"/></svg>

  <div class="area" style="left:65px">
    <div class="icon"><svg width="56" height="40" viewBox="0 0 56 40"><circle cx="15" cy="24" r="11" stroke="#2b2d33" stroke-width="5" fill="none"/><circle cx="41" cy="24" r="11" stroke="#2b2d33" stroke-width="5" fill="none"/><path d="M22 10q6-8 12 0" stroke="#2b2d33" stroke-width="4" fill="none"/></svg></div>
    <h3>Crimimal</h3>
    <p>Lorem ipsum dolor sit amet, consectetuer Lorem dolor sit amet, consectetuer</p>
    <div class="more">[+]</div>
  </div>
  <div class="area" style="left:324px">
    <div class="icon on"><svg width="40" height="54" viewBox="0 0 40 54"><rect x="2" y="2" width="36" height="50" rx="3" fill="#fff"/><circle cx="20" cy="22" r="8" stroke="#2e3038" stroke-width="2" fill="none"/><path d="M12 22h16M20 14v16" stroke="#2e3038" stroke-width="1.5"/><rect x="12" y="40" width="16" height="3" fill="#2e3038"/></svg></div>
    <h3>Citizenship &amp; Residence</h3>
    <p>Lorem ipsum dolor sit amet, consectetuer Lorem dolor sit amet, consectetuer</p>
    <div class="more">[+]</div>
  </div>
  <div class="area" style="left:593px">
    <div class="icon"><svg width="60" height="52" viewBox="0 0 60 52"><path d="M4 10h52M4 18h52M4 26h52" stroke="#2b2d33" stroke-width="2"/><circle cx="30" cy="16" r="9" fill="#2b2d33"/><path d="M14 48l4-18h24l4 18z" fill="#2b2d33"/><rect x="20" y="32" width="20" height="10" fill="#fff"/></svg></div>
    <h3>Criminal Defence</h3>
    <p>Lorem ipsum dolor sit amet, consectetuer Lorem dolor sit amet, consectetuer</p>
    <div class="more">[+]</div>
  </div>
  <div class="area" style="left:867px">
    <div class="icon"><svg width="56" height="52" viewBox="0 0 56 52"><g transform="rotate(-45 28 22)"><rect x="14" y="6" width="28" height="12" fill="#2b2d33"/><rect x="25" y="18" width="6" height="26" fill="#2b2d33"/></g><rect x="6" y="44" width="30" height="6" fill="#2b2d33"/></svg></div>
    <h3>Civil Litigation</h3>
    <p>Lorem ipsum dolor sit amet, consectetuer Lorem dolor sit amet, consectetuer</p>
    <div class="more">[+]</div>
  </div>
</section>

<section class="cases">
  <h2 class="sec-title" style="top:58px">Case Studies</h2>
  <article class="case" style="left:69px">
    <div class="photo" role="img" aria-label="Row of leather-bound law books on a shelf" style="background:linear-gradient(90deg,#3b1d0e,#8a5a2b 30%,#5a2f14 55%,#a27a3e 80%,#4a2612)"><div class="date">06<span>Jun</span></div></div>
    <h4>Lorem Ipsum Dolor Sit Amet Consectetur</h4>
    <p>Lorem ipsum dolor sit amet, consectetur adipiscing elit. Sed vitae magna tellus. Aenean ante nunc, semper nec cursus non, rutrum ac eros.</p>
    <div class="read">Read More &rsaquo;&rsaquo;</div>
  </article>
  <article class="case" style="left:443px">
    <div class="photo" role="img" aria-label="Defendant in handcuffs standing in a courtroom" style="background:linear-gradient(90deg,#4a2414,#7a3e22 40%,#2d2a2c 60%,#3c3436)"><div class="date">06<span>Jun</span></div></div>
    <h4>Lorem Ipsum Dolor Sit Amet Consectetur</h4>
    <p>Lorem ipsum dolor sit amet, consectetur adipiscing elit. Sed vitae magna tellus. Aenean ante nunc, semper nec cursus non, rutrum ac eros.</p>
    <div class="read">Read More &rsaquo;&rsaquo;</div>
  </article>
  <article class="case" style="left:817px">
    <div class="photo" role="img" aria-label="Hands signing a paper contract on a desk" style="background:linear-gradient(120deg,#1f1f22,#4a4a4e 35%,#e9e6e2 60%,#d8d4cf)"><div class="date">07<span>Jun</span></div></div>
    <h4>Lorem Ipsum Dolor Sit Amet Consectetur</h4>
    <p>Lorem ipsum dolor sit amet, consectetur adipiscing elit. Sed vitae magna tellus. Aenean ante nunc, semper nec cursus non, rutrum ac eros.</p>
    <div class="read">Read More &rsaquo;&rsaquo;</div>
  </article>
  <div class="pill-btn" style="left:537px;top:453px"><span>View All</span><i><svg width="10" height="12" viewBox="0 0 10 12"><path d="M2 1l5 5-5 5" stroke="#fff" stroke-width="2" fill="none"/></svg></i></div>
</section>

<section class="testimonials">
  <h2 class="sec-title" style="top:58px">Client Testimonials</h2>
  <svg class="chev" style="left:28px;top:170px" viewBox="0 0 20 60"><path d="M16 2L4 30l12 28" stroke="#444" stroke-width="1.5" fill="none"/></svg>
  <svg class="chev" style="left:1152px;top:170px" viewBox="0 0 20 60"><path d="M4 2l12 28L4 58" stroke="#444" stroke-width="1.5" fill="none"/></svg>
  <div class="portrait" role="img" aria-label="Portrait photo of the client"></div>
  <span class="qmark" style="left:308px;top:100px">&ldquo;</span>
  <p class="quote">Lorem ipsum dolor sit amet, consectetuer adipiscing elit, sed diam nonummy nibh euismod tincidunt ut laoreet dolore magna aliquam erat volutpat. Ut wisi enim ad minim veniam, quis nostrud exerci iriure dolor in Lorem ipsum dolor sit amet, consectetuer adipiscing elit, sed diam nonummy nibh euismod tincidunt ut laoreet dolore magna aliquam erat volutpat. Ut wisi enim ad minim veniam, quis nostrud exerci iriure dolo.</p>
  <span class="qmark" style="left:535px;top:178px">&rdquo;</span>
  <div class="client">- Daniel Borg</div>
</section>

<section class="cta">
  <p>For Any Legal Problem, We Can Help You<br>Anytime take An Appointment Now</p>
  <div class="btn">CONTACT US</div>
</section>

<footer class="site-footer">
  <h5 style="left:67px;width:142px">Quick Links</h5>
  <ul class="quick">
    <li>Home</li><li>About Malta</li><li>Practice Areas</li><li>Our Firm</li><li>Our Values</li><li>What Others Say</li><li>Contact Us</li>
  </ul>
  <h5 style="left:301px;width:490px">Contact Details</h5>
  <div class="map" role="img" aria-label="Street map showing the office location"></div>
  <div class="details">
    <div class="row"><svg viewBox="0 0 14 14"><path d="M7 1a4 4 0 0 1 4 4c0 3-4 8-4 8S3 8 3 5a4 4 0 0 1 4-4z" fill="#fff"/><circle cx="7" cy="5" r="1.5" fill="#2e3038"/></svg><div>Galea &amp; Mifsud Advocates<br>12/4, Harbour Lane, Valletta<br>88, Orchard Road, Birkirkara</div></div>
    <div class="row"><svg viewBox="0 0 14 14"><path d="M3 1l3 3-2 2q2 3 4 4l2-2 3 3-2 2Q5 12 1 3z" fill="#fff"/></svg><div>555-010-204</div></div>
    <div class="row"><svg viewBox="0 0 14 14"><rect x="1" y="5" width="12" height="6" fill="#fff"/><rect x="3" y="1" width="8" height="4" fill="#fff"/><rect x="3" y="9" width="8" height="4" fill="#fff" stroke="#2e3038"/></svg><div>555-010-204</div></div>
    <div class="row"><svg viewBox="0 0 14 14"><rect x="1" y="3" width="12" height="8" fill="#fff"/><path d="M1 3l6 5 6-5" stroke="#2e3038" fill="none"/></svg><div>info@galeamifsud.com</div></div>
  </div>
  <div class="foot-brand">Galea &amp; Mifsud<small>Advocates</small></div>
  <div class="social"><span style="background:#3b5998"></span><span style="background:#0e76a8"></span><span style="background:#1da1f2"></span><span style="background:#dd4b39"></span></div>
</footer>

<div class="legal">
  <div class="copy">Copyright &copy; 2016 <b>Galea &amp; Mifsud Advocates</b>. All Rights Reserved.</div>
  <div class="links">Terms &amp; Conditions &nbsp;|&nbsp; Privacy Policy &nbsp;|&nbsp; Disclaimer</div>
</div>

</body>
</html>
```